Home page design for Drone video business (the Business focusses on home videos for realtors)

Dear reader,

*I NEED DESIGNS OF ALL THE PAGES*
We need a first design of a homepage and of 4 other pages of the website of a business that sells drone video services. All the pages will need to be in the similar design style.
The video's are targeted at consumers that want to sell there home and would like to have a cool drone video of photos of their home.

How does the website look:
- has a navbar on top
- A cool looking banner of an areal drone.
- A Big header: with company name: SkyLoftReels
- A smaller subheader: We film your home to increase your chances of sale
- Then a section with a Big header: How does it work
- In this section a place for a vimeo explainitory video
- Then a similar navbar styled bar with a phone number and a email address
- Then a section where the videos porfolio is displayed in a cool way
- Inside this sectiona header: Our work

- A section with header: Why us?
- 4 symbols here with a subheader and some lorum ipsum text underneath (see wireframe images)

- Under that a: Contact us
- where you can put in name, email, phone, message box and a send button

- At the bottom a footer with phone number and a fake address for now.

Be creative. Use creative but serious color.
Use a serious font. Make it a sharp design. Sharp lines. Not to dark design and not to light design.

The wireframes are the same kind of images.
PLEASE PUT IN DESIGNS OF ALL THE PAGES

Good luck

Target Market(s)

People that want to sell home and want to make a cool drone video or photos of their home.

Industry/Entity Type

Business

Contact Information for Business Card

Lucas Wenning
lucas@skyloftreels.example
+31647208351

Logo Text

SkyLoftReels

Number of Pages Required

1 page

Font styles to use
Sans Serif

Requirements
Must have
• All the sections as explained in the instructions.
• The nav bar should have an about us, services, portfolio and a contact us buttons.
• See instruction for details.
• Must include designs of the front page, contact us, our services, portfolio and contact us.
• If you do add some designs for the "about us", "services", "prices", "portfolio" and "contact us" pages, you make a way better chance of winning the competition.
Nice to have
• designs for the other pages as described at the Must haves. You make a better chance of winning if you include them. Look at the wireframes to see the mockups for those pages. think creative about what kind of sections and design should be included in those pages.
Should not have
• bad designs.

```html
<!DOCTYPE html>
<html lang="en">
<head>
<meta charset="utf-8">
<title>SkyLoftReels – Home</title>
<link rel="stylesheet" href="https://fonts.googleapis.com/css2?family=Exo+2:wght@600;700&family=Lato:wght@400;700&display=swap">
<style>
  :root{
    --red:#a31b1f;
    --ink:#1f1f1f;
    --nav-ink:#222;
    --light-bg:#f0f0f0;
    --white:#ffffff;
    --line:#c9c9c9;
    --footer:#1e1e1e;
    --why-top:#2c3b4f;
    --why-bottom:#415a72;
    --sky-top:#6f9fc0;
    --sky-bottom:#c9d8df;
  }
  *{box-sizing:border-box;margin:0;padding:0}
  html,body{width:1200px;height:2446px;overflow:hidden}
  body{position:relative;background:var(--white);font-family:"Lato",Arial,sans-serif;color:var(--ink)}
  .abs{position:absolute}

  /* Navigation */
  .site-nav{left:0;top:0;width:1200px;height:65px;background:var(--white);border-bottom:1px solid #ddd}
  .brand{left:100px;top:14px;font-family:"Lato",sans-serif;font-weight:700;font-size:28px;color:var(--ink);letter-spacing:.5px;display:flex;align-items:center;gap:10px}
  .brand-dot{width:14px;height:14px;border-radius:50%;background:var(--ink)}
  .nav-links{right:96px;top:19px;display:flex;list-style:none;align-items:center}
  .nav-links li{font-family:"Lato",sans-serif;font-weight:700;font-size:15px;color:var(--nav-ink);padding:0 25px;border-left:1px solid #bbb;line-height:16px}
  .nav-links li:first-child{border-left:none}
  .nav-links li.active{color:var(--red);border:2px solid var(--red);padding:6px 18px;margin-right:14px}
  .nav-links li.active + li{border-left:none}

  /* Hero */
  .hero{left:0;top:65px;width:1200px;height:496px;background:linear-gradient(180deg,var(--sky-top) 0%,#9dbccd 55%,#8a8f93 82%,#4a4a4c 100%)}
  .hero-title{left:0;width:1200px;top:304px;text-align:center;font-family:"Lato",sans-serif;font-weight:700;font-size:43px;color:var(--white);text-shadow:0 2px 8px rgba(0,0,0,.45)}
  .hero-sub{left:0;width:1200px;top:364px;text-align:center;font-family:"Lato",sans-serif;font-weight:700;font-size:29px;line-height:39px;color:var(--white);text-shadow:0 2px 8px rgba(0,0,0,.45)}
  .hero-dots{left:570px;top:532px;display:flex;gap:6px}
  .hero-dots span{width:10px;height:10px;border-radius:50%;background:rgba(255,255,255,.6)}
  .hero-dots span:first-child{background:var(--white)}

  /* Section headings */
  .section-title{left:0;width:1200px;text-align:center;font-family:"Exo 2",sans-serif;font-weight:700;font-size:35px;color:var(--ink);letter-spacing:.5px}
  .section-title em{font-style:normal;color:var(--red)}
  .section-rule{height:1px;background:var(--line)}

  /* How it works */
  .how{left:0;top:561px;width:1200px;height:569px;background:var(--light-bg)}
  .monitor-frame{left:173px;top:727px;width:503px;height:312px;background:#111;border-radius:12px}
  .monitor-screen{left:196px;top:750px;width:458px;height:260px;background:linear-gradient(180deg,#8fb4cf 0%,#5d86a4 55%,#3e5466 100%)}
  .monitor-stand{left:330px;top:1039px;width:190px;height:91px}
  .play-btn{left:385px;top:852px;width:56px;height:56px}
  .contact-line{left:708px;display:flex;align-items:center;gap:18px;font-family:"Lato",sans-serif;font-size:27px;color:var(--ink);white-space:nowrap}
  .icon-ring{width:72px;height:72px;border-radius:50%;border:2px solid var(--red);display:flex;align-items:center;justify-content:center;flex:none}
  .divider-tick{left:618px;top:1084px;width:1px;height:76px;background:#d6d6d6}

  /* Our work */
  .work-card{top:1288px;width:293px;height:249px;background:var(--white);border:1px solid #ddd;padding:8px}
  .work-thumb{width:100%;height:231px;position:relative}
  .work-thumb .play{position:absolute;left:120px;top:95px}
  .thumb-a{background:linear-gradient(180deg,#6c9cd0 0%,#a9c5e0 50%,#c9b68d 80%,#7a8a5a 100%)}
  .thumb-b{background:linear-gradient(180deg,#b9c2c9 0%,#d2d4d2 45%,#a89a80 75%,#6f7656 100%)}
  .thumb-c{background:linear-gradient(180deg,#9fb3c9 0%,#8c8a80 45%,#5e5647 70%,#e3e6ea 100%)}
  .slider-arrow{top:1384px;width:30px;height:56px}

  /* Why us */
  .why{left:0;top:1597px;width:1200px;height:393px;background:linear-gradient(180deg,var(--why-top) 0%,var(--why-bottom) 70%,#5b7389 100%)}
  .why-title{color:var(--white)}
  .feature{top:1718px;width:230px;text-align:center;color:var(--white)}
  .feature-icon{width:110px;height:110px;margin:0 auto;border-radius:50%;border:3px solid var(--white);display:flex;align-items:center;justify-content:center}
  .feature-icon.is-accent{background:var(--red)}
  .feature h3{margin-top:18px;font-family:"Exo 2",sans-serif;font-weight:700;font-size:17px;letter-spacing:.3px}
  .feature p{margin-top:14px;font-size:13px;line-height:20px}

  /* Contact */
  .contact{left:0;top:1990px;width:1200px;height:408px;background:linear-gradient(135deg,#f4f1e6 0%,#eef0ea 50%,#e6eef2 100%)}
  .field{height:43px;background:rgba(255,255,255,.85);border:1px solid #bdbdbd;font-size:13px;color:#333;padding:13px 12px}
  .message{left:124px;top:2184px;width:952px;height:92px}
  .submit{left:536px;top:2305px;width:127px;height:41px;background:var(--red);color:var(--white);font-family:"Lato",sans-serif;font-weight:700;font-size:15px;text-align:center;line-height:41px;letter-spacing:.5px}

  /* Footer */
  .site-footer{left:0;top:2398px;width:1200px;height:48px;background:var(--footer);color:var(--white);font-size:15px}
  .footer-item{top:0;height:48px;display:flex;align-items:center;gap:12px}
  .copyright{right:96px;top:0;line-height:48px;font-size:12px;font-weight:700;letter-spacing:.2px}
</style>
</head>
<body>

<header class="abs site-nav">
  <div class="abs brand"><span class="brand-dot"></span>SkyLoftReels</div>
  <ul class="abs nav-links">
    <li class="active">HOME</li>
    <li>SERVICES</li>
    <li>ABOUT US</li>
    <li>PORTFOLIO</li>
    <li>CONTACT US</li>
  </ul>
</header>

<section class="abs hero" role="img" aria-label="Aerial photo of a hovering camera drone above a city skyline"></section>
<h1 class="abs hero-title">SKYLOFTREELS</h1>
<p class="abs hero-sub">WE FILM YOUR HOME TO<br>INCREASE YOUR CHANCES OF SALE</p>
<div class="abs hero-dots"><span></span><span></span><span></span><span></span></div>

<section class="abs how"></section>
<h2 class="abs section-title" style="top:608px">HOW DOES IT <em>WORK?</em></h2>
<div class="abs section-rule" style="left:404px;top:668px;width:401px"></div>

<div class="abs monitor-frame"></div>
<div class="abs monitor-screen" role="img" aria-label="Explainer video still of a red drone flying over a city bay"></div>
<svg class="abs play-btn" viewBox="0 0 56 56"><circle cx="28" cy="28" r="28" fill="#fff" opacity=".92"/><path d="M22 16 L40 28 L22 40 Z" fill="#555"/></svg>
<svg class="abs monitor-stand" viewBox="0 0 190 91"><path d="M45 0 H145 L150 55 Q185 70 190 91 H0 Q5 70 40 55 Z" fill="#111"/></svg>

<div class="abs contact-line" style="top:800px">
  <span class="icon-ring"><svg width="34" height="34" viewBox="0 0 24 24"><path d="M6.6 10.8a15.1 15.1 0 0 0 6.6 6.6l2.2-2.2c.3-.3.7-.4 1-.2 1.1.4 2.3.6 3.6.6.6 0 1 .4 1 1V20c0 .6-.4 1-1 1A17 17 0 0 1 3 4c0-.6.4-1 1-1h3.5c.6 0 1 .4 1 1 0 1.3.2 2.5.6 3.6.1.3 0 .7-.2 1z" fill="var(--red)"/></svg></span>
  <span>+31647208351</span>
</div>
<div class="abs contact-line" style="top:906px">
  <span class="icon-ring"><svg width="36" height="28" viewBox="0 0 36 28"><rect x="1" y="1" width="34" height="26" fill="var(--red)"/><path d="M1 1 L18 15 L35 1" stroke="#fff" stroke-width="2" fill="none"/><path d="M1 27 L13 12 M35 27 L23 12" stroke="#fff" stroke-width="2"/></svg></span>
  <span>contact@skyloftreels.example</span>
</div>
<div class="abs divider-tick"></div>

<h2 class="abs section-title" style="top:1187px">OUR <em>WORK?</em></h2>
<div class="abs section-rule" style="left:467px;top:1246px;width:266px"></div>

<svg class="abs slider-arrow" style="left:42px" viewBox="0 0 30 56"><path d="M28 2 L3 28 L28 54" stroke="#bbb" stroke-width="2" fill="none"/></svg>
<svg class="abs slider-arrow" style="left:1126px" viewBox="0 0 30 56"><path d="M2 2 L27 28 L2 54" stroke="#bbb" stroke-width="2" fill="none"/></svg>

<article class="abs work-card" style="left:99px">
  <div class="work-thumb thumb-a" role="img" aria-label="Drone pilot with remote in front of a suburban house, drone overhead">
    <svg class="play" width="40" height="40" viewBox="0 0 40 40"><circle cx="20" cy="20" r="20" fill="rgba(0,0,0,.55)"/><path d="M15 11 L29 20 L15 29 Z" fill="#fff"/></svg>
  </div>
</article>
<article class="abs work-card" style="left:453px">
  <div class="work-thumb thumb-b" role="img" aria-label="Drone hovering above a two-storey family home">
    <svg class="play" width="40" height="40" viewBox="0 0 40 40"><circle cx="20" cy="20" r="20" fill="rgba(0,0,0,.55)"/><path d="M15 11 L29 20 L15 29 Z" fill="#fff"/></svg>
  </div>
</article>
<article class="abs work-card" style="left:807px">
  <div class="work-thumb thumb-c" role="img" aria-label="Drone flying over a large house in winter snow">
    <svg class="play" width="40" height="40" viewBox="0 0 40 40"><circle cx="20" cy="20" r="20" fill="rgba(0,0,0,.55)"/><path d="M15 11 L29 20 L15 29 Z" fill="#fff"/></svg>
  </div>
</article>

<section class="abs why" role="img" aria-label="Aerial view of a coastal city with a white drone in the sky, darkened"></section>
<h2 class="abs section-title why-title" style="top:1622px">WHY US?</h2>
<div class="abs section-rule" style="left:450px;top:1680px;width:302px;background:rgba(255,255,255,.45)"></div>

<div class="abs feature" style="left:82px">
  <div class="feature-icon is-accent"><svg width="58" height="58" viewBox="0 0 58 58" fill="none" stroke="#fff" stroke-width="3"><circle cx="12" cy="12" r="8"/><circle cx="46" cy="12" r="8"/><circle cx="12" cy="46" r="8"/><circle cx="46" cy="46" r="8"/><path d="M18 18 L40 40 M40 18 L18 40"/><rect x="23" y="23" width="12" height="12" fill="#fff"/></svg></div>
  <h3>CHEAP</h3>
  <p>Lorem ipsum dolor sit amet,<br>consectetuer sit al adipiscing elit,<br>sed diam nonummy.</p>
</div>
<div class="abs feature" style="left:335px">
  <div class="feature-icon"><svg width="58" height="58" viewBox="0 0 58 58" fill="none" stroke="#fff" stroke-width="3"><circle cx="14" cy="14" r="10"/><circle cx="44" cy="14" r="10"/><circle cx="14" cy="44" r="10"/><circle cx="44" cy="44" r="10"/><circle cx="29" cy="29" r="7" fill="#fff"/></svg></div>
  <h3>FLEXIBLE</h3>
  <p>Lorem ipsum dolor sit amet,<br>consectetuer sit al adipiscing elit,<br>sed diam nonummy.</p>
</div>
<div class="abs feature" style="left:589px">
  <div class="feature-icon"><svg width="58" height="50" viewBox="0 0 58 50"><rect x="3" y="3" width="52" height="34" fill="none" stroke="#fff" stroke-width="3"/><text x="29" y="28" text-anchor="middle" font-family="Lato,sans-serif" font-weight="700" font-size="18" fill="#fff">4K</text><path d="M20 46 H38" stroke="#fff" stroke-width="3"/></svg></div>
  <h3>4K QUALITY</h3>
  <p>Lorem ipsum dolor sit amet,<br>consectetuer sit al adipiscing elit,<br>sed diam nonummy.</p>
</div>
<div class="abs feature" style="left:856px">
  <div class="feature-icon"><svg width="62" height="50" viewBox="0 0 62 50" fill="none" stroke="#fff" stroke-width="3"><path d="M4 8 H24 M38 8 H58 M14 8 V16 M48 8 V16"/><rect x="14" y="16" width="34" height="12" fill="#fff"/><path d="M20 28 L12 44 M42 28 L50 44 M6 44 H18 M44 44 H56"/></svg></div>
  <h3>INCREASE SALE CHANCE</h3>
  <p>Lorem ipsum dolor sit amet,<br>consectetuer sit al adipiscing elit,<br>sed diam nonummy.</p>
</div>

<section class="abs contact" role="img" aria-label="Faded street map of the business neighbourhood"></section>
<h2 class="abs section-title" style="top:2034px">CONTACT <em>US</em></h2>
<div class="abs field" style="left:124px;top:2117px;width:300px">Name</div>
<div class="abs field" style="left:448px;top:2117px;width:300px">Name</div>
<div class="abs field" style="left:776px;top:2117px;width:300px">Name</div>
<div class="abs field message">Message</div>
<div class="abs submit">SUBMIT</div>

<footer class="abs site-footer">
  <div class="abs footer-item" style="left:98px">
    <svg width="18" height="22" viewBox="0 0 24 24"><path d="M6.6 10.8a15.1 15.1 0 0 0 6.6 6.6l2.2-2.2c.3-.3.7-.4 1-.2 1.1.4 2.3.6 3.6.6.6 0 1 .4 1 1V20c0 .6-.4 1-1 1A17 17 0 0 1 3 4c0-.6.4-1 1-1h3.5c.6 0 1 .4 1 1 0 1.3.2 2.5.6 3.6.1.3 0 .7-.2 1z" fill="#fff"/></svg>
    <span>+31647208351</span>
  </div>
  <div class="abs footer-item" style="left:262px">
    <svg width="24" height="18" viewBox="0 0 36 28"><rect x="1" y="1" width="34" height="26" fill="#fff"/><path d="M1 1 L18 15 L35 1" stroke="#1e1e1e" stroke-width="3" fill="none"/></svg>
    <span>contact@skyloftreels.example</span>
  </div>
  <div class="abs copyright">COPYRIGHT © 2016 SKYLOFTREELS. ALL RIGHTS RESERVED.</div>
</footer>

</body>
</html>
```